I need to make a car magnet

It needs to include the words "PLAVO TOUR" and "2026 MEMBER" as well as the attached silhouette of the golfer. The color scheme needs to be navy, red and white. The shape and dimensions are open for interpretation

```html
<!DOCTYPE html>
<html lang="en">
<head>
<meta charset="utf-8">
<title>Plavo Tour – 2026 Member Car Magnet</title>
<link rel="stylesheet" href="https://fonts.googleapis.com/css2?family=Russo+One&display=swap">
<style>
  :root {
    --navy: #1d2b5c;
    --red: #e32330;
    --white: #ffffff;
    --backdrop: #b0b0b0;
  }
  html, body {
    margin: 0;
    padding: 0;
    width: 892px;
    height: 1200px;
    overflow: hidden;
    background: var(--backdrop);
  }
  .canvas {
    position: relative;
    width: 892px;
    height: 1200px;
  }
  .car-magnet {
    position: absolute;
    left: 46px;
    top: 400px;
    width: 800px;
    height: 400px;
    box-shadow: 2px 3px 6px rgba(0, 0, 0, 0.35);
    background: var(--white);
  }
  .car-magnet svg {
    display: block;
    width: 800px;
    height: 400px;
  }
  .headline {
    font-family: "Russo One", sans-serif;
  }
  .headline--brand { fill: var(--red); }
  .headline--tour { fill: var(--navy); }
  .membership-year {
    font-family: "Russo One", sans-serif;
    fill: var(--navy);
  }
  .wave--navy { fill: var(--navy); }
  .wave--red { fill: var(--red); }
  .golfer-silhouette { fill: var(--navy); }
</style>
</head>
<body>
<main class="canvas">
  <section class="car-magnet">
    <svg viewBox="0 0 800 400" xmlns="http://www.w3.org/2000/svg">
      <rect class="magnet-base" width="800" height="400" fill="var(--white)"/>

      <path class="wave wave--navy"
            d="M0,304 C40,370 120,395 260,392 C450,390 650,360 800,362 L800,400 L0,400 Z"/>
      <path class="wave wave--red"
            d="M82,374 C300,390 500,330 650,294 C720,290 770,305 800,322 L800,350 C650,338 450,370 300,382 C200,385 120,380 82,374 Z"/>

      <rect class="golfer-silhouette" x="612" y="20" width="146" height="276" rx="10"
            role="img" aria-label="Navy silhouette of a golfer putting toward the hole"/>

      <g transform="skewX(-12)">
        <text class="headline headline--brand" x="60" y="119" font-size="108"
              textLength="515" lengthAdjust="spacingAndGlyphs">PLAVO</text>
        <text class="headline headline--tour" x="145" y="217" font-size="108"
              textLength="390" lengthAdjust="spacingAndGlyphs">TOUR</text>
        <text class="membership-year" x="188" y="279" font-size="37"
              textLength="340" lengthAdjust="spacingAndGlyphs">2026 MEMBER</text>
      </g>
    </svg>
  </section>
</main>
</body>
</html>
```